Simple and Clean business card design

We would like the design to be simple clean and to incorporate our colors.

We are open to your design and talent, we have the dots in our logo as we think of it as data points and we connect data points for people.

We are open to see the great creative and clean design you bring to the table

Contact Information for Business Card

please include: name, position, email, phone and website

Font styles to use
Sans Serif

Requirements
Must have
• my colors incorporated, simplicity
Nice to have
• lots of white space, simplicity
Should not have
• complexicity/ complex art

```html
<!DOCTYPE html>
<html lang="en">
<head>
<meta charset="utf-8">
<title>Nodelo Business Card</title>
<link href="https://fonts.googleapis.com/css2?family=Arimo:wght@400;700&display=swap" rel="stylesheet">
<style>
  :root{
    --stage:#2a2a2b;
    --blue:#4285f4;
    --green:#34a853;
    --yellow:#f4b400;
    --red:#ea4335;
    --ink:#111111;
    --paper:#ffffff;
  }
  html,body{margin:0;padding:0;overflow:hidden;}
  body{
    width:1200px;height:901px;background:var(--stage);
    font-family:"Arimo",Arial,sans-serif;position:relative;
  }
  .card{
    position:absolute;left:290px;width:620px;height:354px;
    box-shadow:0 10px 30px rgba(0,0,0,.45);overflow:hidden;
  }
  .card-front{top:44px;}
  .front-art{
    position:absolute;inset:0;
    background:linear-gradient(135deg,var(--blue) 0%,#3b9fc4 55%,var(--green) 100%);
  }
  .front-wordmark{
    position:absolute;left:0;right:0;top:136px;text-align:center;
    color:var(--paper);font-weight:700;font-size:76px;letter-spacing:2px;line-height:1;
  }
  .card-back{top:456px;background:var(--paper);}
  .back-art{
    position:absolute;left:0;top:0;width:620px;height:210px;
    background:linear-gradient(90deg,#6aa2f7 0%,#c9d6f2 100%);
    clip-path:ellipse(75% 78% at 50% 0%);
  }
  .person{position:absolute;left:40px;top:190px;}
  .person-name{color:var(--blue);font-weight:700;font-size:26px;margin:0;line-height:1.1;}
  .person-role{color:var(--ink);font-size:17px;margin:4px 0 0;}
  .divider{position:absolute;left:36px;right:40px;top:252px;height:1.5px;background:var(--ink);}
  .contacts{position:absolute;left:40px;top:262px;list-style:none;margin:0;padding:0;}
  .contacts li{display:flex;align-items:center;gap:10px;font-size:18px;color:var(--ink);height:27px;}
  .contacts svg{width:20px;height:20px;flex:none;}
  .back-wordmark{
    position:absolute;right:44px;top:176px;display:flex;align-items:center;gap:10px;
    color:var(--ink);font-weight:700;font-size:60px;line-height:1;
  }
  .back-wordmark .dot{width:18px;height:18px;border-radius:50%;background:var(--blue);}
  .address{
    position:absolute;right:44px;bottom:26px;text-align:right;
    font-size:17px;line-height:1.35;color:var(--ink);
  }
</style>
</head>
<body>
  <section class="card card-front">
    <div class="front-art" role="img" aria-label="Soft colour field in the brand blue and green"></div>
    <div class="front-wordmark">Nodelo</div>
  </section>

  <section class="card card-back">
    <div class="back-art" role="img" aria-label="Soft brand colour band across the top of the card"></div>

    <div class="person">
      <p class="person-name">Daniel Reyes</p>
      <p class="person-role">Manager</p>
    </div>
    <div class="divider"></div>
    <ul class="contacts">
      <li>
        <svg viewBox="0 0 20 20" aria-hidden="true"><rect width="20" height="20" rx="4" fill="var(--blue)"/><path d="M6,4 L8.5,4 L9.5,7 L8,8.3 Q9.5,11.5 11.7,12 L13,10.5 L16,11.5 L16,14 Q15,16 12.5,15.5 Q5,13 4.5,6.5 Q4.5,4.5 6,4 Z" fill="#fff"/></svg>
        555-014-2100
      </li>
      <li>
        <svg viewBox="0 0 20 20" aria-hidden="true"><rect width="20" height="20" rx="4" fill="var(--blue)"/><rect x="4" y="6" width="12" height="8" fill="none" stroke="#fff" stroke-width="1.5"/><path d="M4,6 L10,11 L16,6" fill="none" stroke="#fff" stroke-width="1.5"/></svg>
        hello@nodelo.com
      </li>
      <li>
        <svg viewBox="0 0 20 20" aria-hidden="true"><rect width="20" height="20" rx="4" fill="var(--blue)"/><circle cx="10" cy="10" r="6" fill="none" stroke="#fff" stroke-width="1.5"/><path d="M4,10 H16 M10,4 Q6.5,10 10,16 M10,4 Q13.5,10 10,16" fill="none" stroke="#fff" stroke-width="1.2"/></svg>
        www.nodelo.com
      </li>
    </ul>

    <div class="back-wordmark"><span class="dot"></span>Nodelo</div>

    <div class="address">Your address, city<br>state, ZIP 0000</div>
  </section>
</body>
</html>
```